Tech Savy small Business accountant business card design

We need a business card for a new company based in the cloud. We provide tax, business advisory, accounting, information technology solutions and back office functions to small businesses. We offer fixed fee packages with add on services as you need them. By harnessing technology we simplify small business operational processes providing valuable time and information for small business owners to grow their business. In the logo (bluvoria) we want to be able to see bluv and experts. The final design should communicate achieving growth dreams and balance (ie life and $).
Updates
This project has been temporarily placed on hold until I finalize "Tech Savy small Business accountant needs a logo". I invite all designers to submit on this logo project. Once my logo is finalized I will resume this business card contest. Thanks Added Wednesday, March 19, 2014
This project has been temporarily placed on hold until I finalize "Tech Savy small Business accountant logo". I invite all designers to submit on this logo project. Once my logo is finalized I will resume this business card contest. Thanks Added Thursday, March 20, 2014
Target Market(s)
Small Business (Revenue $500,000, more than 3 employees) owners.
Industry/Entity Type
Small Business
Contact Information for Business Card
Marcy Elwind (Principal)
Accountant, Tax Agent.
TEL | 0417 683 912
EMAIL | Marcy.Elwind@bluvoria.com.au
WEB | www.bluvoria.com.au
Look and feel

```html
<!DOCTYPE html>
<html lang="en">
<head>
<meta charset="utf-8">
<title>bluvoria business card</title>
<link rel="stylesheet" href="https://fonts.googleapis.com/css2?family=Questrial&display=swap">
<style>
  :root {
    --bg: #3b3430;
    --card: #141414;
    --card-edge: #1d1d1d;
    --blue: #1c8fd4;
    --white: #f2f2f2;
  }
  * { margin: 0; padding: 0; box-sizing: border-box; }
  html, body { width: 1200px; height: 780px; overflow: hidden; }
  body {
    background: var(--bg);
    font-family: "Questrial", "Century Gothic", sans-serif;
    display: flex;
    align-items: center;
    justify-content: center;
    gap: 40px;
  }
  .card {
    position: relative;
    width: 540px;
    height: 330px;
    background: var(--card);
    border: 1px solid var(--card-edge);
    border-radius: 4px;
    box-shadow: 0 12px 30px rgba(0,0,0,.45);
    color: var(--white);
  }
  .brand { position: absolute; }
  .brand-name {
    color: var(--blue);
    font-size: 64px;
    line-height: 1;
    letter-spacing: -1px;
  }
  .brand-tagline {
    font-size: 15px;
    color: var(--white);
    margin-top: 4px;
    letter-spacing: .3px;
  }
  .card-front .brand { left: 50%; top: 50%; transform: translate(-50%, -55%); }
  .card-back .brand { left: 110px; top: 40px; }
  .card-back .brand-name { font-size: 56px; }
  .divider {
    position: absolute;
    left: 36px;
    width: 300px;
    top: 172px;
    height: 1.5px;
    background: var(--blue);
  }
  .contact {
    position: absolute;
    left: 30px; top: 196px;
    list-style: none;
    font-size: 15px;
    line-height: 23px;
  }
  .contact li { display: flex; align-items: center; gap: 9px; }
  .contact svg { width: 15px; height: 15px; flex: none; }
  .person {
    position: absolute;
    right: 30px; top: 150px;
    text-align: right;
  }
  .person-name { color: var(--blue); font-size: 27px; line-height: 1.1; }
  .person-role { font-size: 15px; line-height: 19px; }
  .location { margin-top: 22px; font-size: 15px; line-height: 19px; }
</style>
</head>
<body>
  <section class="card card-front">
    <div class="brand">
      <div class="brand-name">bluvoria</div>
      <div class="brand-tagline">Your business and accounting partner</div>
    </div>
  </section>

  <section class="card card-back">
    <div class="brand">
      <div class="brand-name">bluvoria</div>
      <div class="brand-tagline">Your business and accounting partner</div>
    </div>
    <div class="divider"></div>
    <ul class="contact">
      <li>
        <svg viewBox="0 0 16 16" aria-hidden="true"><rect width="16" height="16" rx="2" fill="#1c8fd4"/><path d="M4 5.5c0-1 1-1.5 1.5-1.5l1 2-1 1c.5 1.2 1.3 2 2.5 2.5l1-1 2 1c0 .5-.5 1.5-1.5 1.5C6.5 11 4 8.5 4 5.5z" fill="#fff"/></svg>
        0417 683 912
      </li>
      <li>
        <svg viewBox="0 0 16 16" aria-hidden="true"><rect width="16" height="16" rx="2" fill="#1c8fd4"/><rect x="3" y="4.5" width="10" height="7" fill="none" stroke="#fff" stroke-width="1.2"/><path d="M3 4.5l5 4 5-4" fill="none" stroke="#fff" stroke-width="1.2"/></svg>
        Marcy.Elwind@bluvoria.com.au
      </li>
      <li>
        <svg viewBox="0 0 16 16" aria-hidden="true"><circle cx="8" cy="8" r="8" fill="#1c8fd4"/><circle cx="8" cy="8" r="5" fill="none" stroke="#fff" stroke-width="1"/><ellipse cx="8" cy="8" rx="2.2" ry="5" fill="none" stroke="#fff" stroke-width="1"/><path d="M3 8h10" stroke="#fff" stroke-width="1"/></svg>
        www.bluvoria.com.au
      </li>
    </ul>
    <div class="person">
      <div class="person-name">Marcy Elwind</div>
      <div class="person-role">(Principal)</div>
      <div class="person-role">Accountant, Tax Agent</div>
      <div class="location">Kellmore NSW<br>Australia</div>
    </div>
  </section>
</body>
</html>
```